Brightwell Aero Services Logo

I need a website and logo for the parent company Brightwell Aero Services, which encompasses general aviation aircraft repair, small aircrat rental and flight school. The company is based in Lawrenceville, Georgia at the Tolleson county airport. A saying that can be incorporated somehere could be, "Quality flying is safe flying", "Safety in mind is no accident" ,. I need a website and logo.

The company started as a repair shop performing repairs and inspections on Harlan, Vantor, Delkin and Ralstead general aviation aircraft, all models of single engine piston, multi engine piston, and single engine turboprop with an emphasis on Harlan Solvane and AeroTurn turbo prop aircraft. We have se=ince entered the aircraft rental and flight instruction market using the Delkin 240 ang Harlan Ranger aircraft.

Number of Pages; I don't know. Maybe 5 ? A home page for Brightwell Aero Services, page for maintenance and repairs and a couple for the rental and school. The maintenance shop is busy, always has been. I need to get the rental and school advertised and busy.

I have a logo for the maintenance shop shirts, not for the school. I do not have the file. I paid a business locally to do that and print on the shirts. They have the file.

Target Market(s)

In our flight school rental fleet department, we are looking for persons wishing to obtain their private pilot license and continuing on into their commercial and instrument ratings. In the aircraft maintenance department, we are looking for new customers who want a better and more quality relationship with their aircraft maintenance provider who will give more detail and quality in the repairs with an emphasis on safety and fewer problems between scheduled maintenance cycles on their aircraft. Brightwell's owner, Dale Hutchins, has been performing aircraft maintenance in the Atlanta area for 27 years. He has built a steady customer base through those years.

```html
<!DOCTYPE html>
<html lang="en">
<head>
<meta charset="utf-8">
<title>Brightwell Aero</title>
<link href="https://fonts.googleapis.com/css2?family=Outfit:wght@500;600;700&family=Questrial&family=Arimo:wght@400;700&display=swap" rel="stylesheet">
<style>
:root{
  --navy:#1a4f8a;
  --sky:#ade6fa;
  --sky-soft:#c7eefc;
  --ink:#2b2119;
  --text:#333;
  --card:#f1efec;
  --white:#fff;
}
*{margin:0;padding:0;box-sizing:border-box}
html,body{width:1200px;height:3155px;overflow:hidden;background:var(--white)}
body{position:relative;font-family:'Questrial',sans-serif;color:var(--text)}
.abs{position:absolute}
.brand{font-family:'Outfit',sans-serif;font-weight:600;color:var(--navy);line-height:1;display:flex;align-items:center;gap:10px}
.brand-mark{width:14px;height:14px;background:var(--navy)}
.site-header .brand{left:200px;top:20px;font-size:27px}
.nav{font-family:'Outfit',sans-serif;font-weight:500;font-size:16px;color:#444;text-transform:uppercase}
.nav a{position:absolute;white-space:nowrap;color:inherit;text-decoration:none}
.site-header .nav{left:571px;top:39px}
.hero{left:0;top:90px;width:1200px;height:590px}
.hero-title{left:150px;top:138px;width:595px;text-align:center;font-family:'Outfit',sans-serif;font-weight:700;font-size:66px;line-height:83px;color:var(--white);text-transform:uppercase;letter-spacing:-1px}
.section-title{font-family:'Outfit',sans-serif;font-weight:700;color:var(--navy);font-size:39px;text-transform:uppercase;letter-spacing:-0.5px}
.btn{display:flex;align-items:center;justify-content:center;background:var(--ink);color:var(--white);border-radius:6px;font-family:'Arimo',sans-serif;font-size:13px;width:143px;height:45px;text-decoration:none}
.about-text{left:127px;top:848px;width:570px;font-size:18px;line-height:32.5px;letter-spacing:.25px;color:#333}
.about-frame{left:751px;top:790px;width:449px;height:298px;background:var(--navy)}
.photo{border-radius:4px}
.services{left:0;top:1189px;width:1200px;height:630px;background:var(--sky)}
.card-img{top:170px;width:277px;height:156px}
.card{top:325px;width:336px;height:231px;background:var(--card);text-align:center;font-family:'Arimo',sans-serif}
.card h3{margin-top:82px;font-size:20px;color:#222}
.card p{margin:10px auto 0;width:250px;font-size:15.5px;line-height:25px;letter-spacing:.4px;color:#333}
.card-icon{top:-28px;left:120px;width:94px;height:94px;border-radius:50%;background:var(--white);box-shadow:0 2px 6px rgba(0,0,0,.12);display:flex;align-items:center;justify-content:center}
.card .btn{position:absolute;left:91px;top:209px}
.rental{left:0;top:1819px;width:1200px;height:530px}
.clients{left:0;top:2349px;width:1200px;height:461px;background:var(--sky)}
.client{top:170px;width:255px;height:164px;background:var(--sky-soft);padding:12px}
.client-inner{width:100%;height:100%;background:var(--white);display:flex;align-items:center;justify-content:center;font-family:'Outfit',sans-serif;font-weight:600;font-size:34px;color:#222}
.subscribe{left:492px;top:2885px;width:576px;height:51px;display:flex}
.subscribe .field{flex:0 0 340px;border:1px solid #777;font-family:'Outfit',sans-serif;font-size:17px;color:#666;padding:14px 24px}
.subscribe .go{flex:1;background:var(--navy);color:var(--white);font-family:'Outfit',sans-serif;font-weight:600;font-size:17px;display:flex;align-items:center;justify-content:center}
.site-footer .brand{left:225px;top:2952px;font-size:33px}
.footer-nav{left:557px;top:2981px}
.social{left:700px;top:3057px;display:flex;gap:16px;font-family:'Arimo',sans-serif;font-size:12px;color:#3a8fd6}
.rule{left:486px;top:3098px;width:587px;height:1px;background:var(--navy)}
.copyright{left:0;width:1550px;top:3126px;text-align:center;font-family:'Arimo',sans-serif;font-size:10.5px;color:#1a3f70}
</style>
</head>
<body>

<header class="site-header">
  <div class="abs brand"><span class="brand-mark"></span><span>BRIGHTWELL<br>AERO</span></div>
  <nav class="abs nav">
    <a href="#" style="left:0">Home</a>
    <a href="#" style="left:116px">About Us</a>
    <a href="#" style="left:271px">Services</a>
    <a href="#" style="left:424px">Contact</a>
  </nav>
</header>

<section class="abs hero">
  <svg width="1200" height="590" viewBox="0 0 1200 590" style="position:absolute;left:0;top:0">
    <defs>
      <linearGradient id="city" x1="0" y1="0" x2="0" y2="1">
        <stop offset="0" stop-color="#3b6fb0"/>
        <stop offset=".55" stop-color="#4f86c4"/>
        <stop offset="1" stop-color="#2c5a86"/>
      </linearGradient>
    </defs>
    <rect width="1200" height="590" fill="var(--white)"/>
    <polygon points="760,0 1200,0 1200,580 740,580" fill="var(--sky)"/>
    <polygon points="0,0 845,0 740,555 0,555" fill="url(#city)" role="img" aria-label="City skyline photo with an airliner flying overhead"/>
  </svg>
  <h1 class="abs hero-title">Quality Flying<br>is<br>Safe Flying</h1>
</section>

<section class="about">
  <h2 class="abs section-title" style="left:316px;top:765px">About Us</h2>
  <p class="abs about-text">Lorem Ipsum is simply dummy text of the printing and typesetting industry. Lorem Ipsum has been the industry's standard dummy text ever since the 1500s, when an unknown printer took a galley of type and scrambled it to make a type specimen book. It has survived not only five centuries, but also the leap into electronic typesetting, remaining essentially unchanged.</p>
  <a href="#" class="abs btn" style="left:344px;top:1075px;font-family:'Questrial',sans-serif;font-size:17px">Read More</a>
  <div class="abs about-frame"></div>
  <div class="abs photo" style="left:735px;top:802px;width:435px;height:272px;background:linear-gradient(135deg,#7d8791,#c9ccd0 50%,#5e646b)" role="img" aria-label="Light aircraft parked inside a maintenance hangar"></div>
</section>

<section class="abs services">
  <h2 class="abs section-title" style="left:0;width:1220px;text-align:center;top:80px">Our Services</h2>

  <div class="abs card-img" style="left:91px;background:linear-gradient(120deg,#f0a94a,#8a5a2c 60%,#3d3a36)" role="img" aria-label="Two mechanics beside an aircraft engine at sunset"></div>
  <div class="abs card-img" style="left:460px;background:linear-gradient(180deg,#7fa3c6,#e3e8ee 60%,#a9b4c0)" role="img" aria-label="Small turboprop plane flying above clouds"></div>
  <div class="abs card-img" style="left:826px;background:linear-gradient(135deg,#3a4a52,#7c8b92 50%,#2a3338)" role="img" aria-label="Cockpit instrument panel with a hand pointing"></div>

  <div class="abs card" style="left:61px">
    <div class="abs card-icon"><svg width="54" height="54" viewBox="0 0 54 54" fill="none" stroke="#2c5a86" stroke-width="1.8"><circle cx="27" cy="27" r="16"/><circle cx="27" cy="27" r="7"/><path d="M27 5v6M27 43v6M5 27h6M43 27h6M11 11l4 4M39 39l4 4M11 43l4-4M39 15l4-4"/></svg></div>
    <h3>Maintenance &amp; Repairs</h3>
    <p>Lorem Ipsum is simply dummy text of the printing and typesetting industry.</p>
    <a href="#" class="btn">Read More</a>
  </div>
  <div class="abs card" style="left:431px">
    <div class="abs card-icon"><svg width="54" height="54" viewBox="0 0 54 54" fill="none" stroke="#2c5a86" stroke-width="1.8"><circle cx="18" cy="20" r="9"/><rect x="32" y="9" width="14" height="28" rx="2"/><path d="M8 42h38M18 14v6l4 3"/></svg></div>
    <h3>Small Aircraft Rental</h3>
    <p>Lorem Ipsum is simply dummy text of the printing and typesetting industry.</p>
    <a href="#" class="btn">Read More</a>
  </div>
  <div class="abs card" style="left:797px">
    <div class="abs card-icon"><svg width="54" height="54" viewBox="0 0 54 54" fill="none" stroke="#2c5a86" stroke-width="1.8"><path d="M27 8l18 7v12c0 10-8 16-18 19C17 43 9 37 9 27V15z"/><path d="M18 24l9-4 9 4-9 4z"/></svg></div>
    <h3>Flight School</h3>
    <p>Lorem Ipsum is simply dummy text of the printing and typesetting industry.</p>
    <a href="#" class="btn">Read More</a>
  </div>
</section>

<section class="abs rental">
  <div class="abs" style="left:0;top:0;width:615px;height:530px;background:linear-gradient(160deg,#8fa4b6,#5c6b77 55%,#3d464d)" role="img" aria-label="Aircraft being repaired in a hangar"></div>
  <div class="abs" style="left:615px;top:0;width:585px;height:530px;background:linear-gradient(160deg,#9bb8c9,#d7dde2 45%,#6d7f8e)" role="img" aria-label="Student and instructor seated in a flight simulator"></div>
  <h2 class="abs section-title" style="left:0;width:1236px;text-align:center;top:100px">Rental and School</h2>
  <a href="#" class="abs btn" style="left:227px;top:422px">Click Here</a>
  <a href="#" class="abs btn" style="left:842px;top:424px">Click Here</a>
</section>

<section class="abs clients">
  <h2 class="abs section-title" style="left:0;width:1236px;text-align:center;top:70px">Our Clients</h2>
  <div class="abs client" style="left:84px"><div class="client-inner">Harlan</div></div>
  <div class="abs client" style="left:352px"><div class="client-inner">Ralstead</div></div>
  <div class="abs client" style="left:622px"><div class="client-inner">Delkin</div></div>
  <div class="abs client" style="left:888px"><div class="client-inner">Vantor</div></div>
</section>

<footer class="site-footer">
  <div class="abs subscribe"><div class="field">Your E-mail</div><div class="go">Subscribe Now</div></div>
  <div class="abs brand"><span class="brand-mark"></span><span>BRIGHTWELL<br>AERO</span></div>
  <nav class="abs nav footer-nav">
    <a href="#" style="left:0">Home</a>
    <a href="#" style="left:91px">About Us</a>
    <a href="#" style="left:218px">Services</a>
    <a href="#" style="left:347px">Contact</a>
  </nav>
  <div class="abs social"><span>Linkora</span><span>Chirpa</span><span>Globo</span></div>
  <div class="abs rule"></div>
  <p class="abs copyright">© 2023 Brightwell Aero. All Rights Reserved.</p>
</footer>

</body>
</html>
```